Harbor Crestline (Business Card Design)

Need business cards designed. Something modern, chic, and sleek. Mabye the back of the card should be the navy blue that is in the logo and then just the logo on the back.

Target Market(s)

Those in the hotel, office, and renovation industry

Contact Information for Business Card

1. Logo 2. Dorian Fenwick 3. CEO/Founder 4. Phone: (833) HarbCre / (833) 427-2731 5. Email: dorian@theharborcrestline.com 6. Website: www.theharborcrestline.com

Font styles to use
Other font styles liked:
• Look at the logo font and base the font for everything else off of that.

Colors
0054AA
0677BA
7BADD7
CADEEF
E8F1F8

Requirements
Must have
• Colors that are associated in the logo
Nice to have
• Sleek modern clean and chic design.

```html
<!DOCTYPE html>
<html lang="en">
<head>
<meta charset="utf-8">
<title>Harbor Crestline — Business Card</title>
<link rel="stylesheet" href="https://fonts.googleapis.com/css2?family=Montserrat:wght@700&family=Lato:wght@400;700&display=swap">
<style>
  :root {
    --navy: #0e1840;
    --gold: #c9a043;
    --paper: #ffffff;
    --ink: #2a2f3a;
    --stage: #e9eaed;
    --hairline: #e3e4e8;
  }
  * { box-sizing: border-box; margin: 0; padding: 0; }
  html, body { width: 1200px; height: 900px; overflow: hidden; }
  body {
    background: var(--stage);
    font-family: "Lato", sans-serif;
    position: relative;
  }
  .card {
    position: absolute;
    left: 300px;
    width: 600px;
    height: 343px;
    border-radius: 28px;
    box-shadow: 0 10px 30px rgba(0,0,0,.18);
    overflow: hidden;
  }
  /* Back */
  .card-back { top: 62px; background: var(--navy); }
  .back-brand {
    position: absolute; top: 112px; left: 0; right: 0;
    display: flex; justify-content: center; align-items: center; gap: 12px;
  }
  .brand-mark { width: 12px; height: 12px; background: var(--gold); }
  .back-brand .brand-name {
    font-family: "Montserrat", sans-serif; font-weight: 700;
    font-size: 28px; letter-spacing: 2px; color: var(--paper); text-transform: uppercase;
  }
  .back-rule {
    position: absolute; left: 90px; right: 90px; top: 232px;
    height: 1px; background: var(--paper);
  }
  .back-url {
    position: absolute; top: 252px; left: 0; right: 0; text-align: center;
    font-size: 16px; letter-spacing: 6px; color: var(--paper);
  }
  .back-url .domain { color: var(--gold); }
  /* Front */
  .card-front { top: 485px; background: var(--paper); }
  .front-brand {
    position: absolute; top: 58px; left: 56px;
    display: flex; align-items: center; gap: 12px;
  }
  .front-brand .brand-name {
    font-family: "Montserrat", sans-serif; font-weight: 700;
    font-size: 30px; letter-spacing: 1.5px; color: var(--navy); text-transform: uppercase;
  }
  .identity {
    position: absolute; top: 170px; left: 56px;
    display: flex; align-items: center; gap: 12px;
  }
  .person-name {
    font-weight: 700; font-size: 19px; letter-spacing: 1px;
    color: var(--navy); text-transform: uppercase;
  }
  .divider-bar { width: 1px; height: 22px; background: var(--navy); }
  .person-title { font-size: 17px; color: var(--ink); }
  .front-rule {
    position: absolute; left: 56px; right: 56px; top: 212px;
    height: 1px; background: var(--gold);
  }
  .contacts {
    position: absolute; top: 232px; left: 56px; right: 56px;
    display: flex; gap: 22px;
  }
  .contact-col { display: flex; flex-direction: column; gap: 12px; }
  .contact-split { width: 1px; background: var(--gold); }
  .contact-line {
    display: flex; align-items: center; gap: 10px;
    font-size: 15px; color: var(--ink);
  }
  .contact-line svg { width: 16px; height: 16px; flex: none; }
</style>
</head>
<body>

<section class="card card-back">
  <div class="back-brand">
    <span class="brand-mark"></span>
    <span class="brand-name">Harbor Crestline</span>
  </div>
  <div class="back-rule"></div>
  <p class="back-url">www.<span class="domain">theharborcrestline</span>.com</p>
</section>

<section class="card card-front">
  <div class="front-brand">
    <span class="brand-mark"></span>
    <span class="brand-name">Harbor Crestline</span>
  </div>

  <div class="identity">
    <span class="person-name">Dorian Fenwick</span>
    <span class="divider-bar"></span>
    <span class="person-title">CEO/Founder</span>
  </div>
  <div class="front-rule"></div>

  <div class="contacts">
    <div class="contact-col">
      <p class="contact-line">
        <svg viewBox="0 0 16 16"><path fill="#0e1840" d="M2 6c0-2 2-3 6-3s6 1 6 3v1h-3V6H5v1H2z M4 8h8l1 5H3z"/></svg>
        (833) HarbCre
      </p>
      <p class="contact-line">
        <svg viewBox="0 0 16 16"><path fill="#0e1840" d="M2 6c0-2 2-3 6-3s6 1 6 3v1h-3V6H5v1H2z M4 8h8l1 5H3z"/></svg>
        (833) 427-2731
      </p>
    </div>
    <div class="contact-split"></div>
    <div class="contact-col">
      <p class="contact-line">
        <svg viewBox="0 0 16 16"><rect x="1.5" y="3.5" width="13" height="9" fill="none" stroke="#0e1840" stroke-width="1.5"/><path d="M1.5 3.5l6.5 5 6.5-5" fill="none" stroke="#0e1840" stroke-width="1.5"/></svg>
        dorian@theharborcrestline.com
      </p>
      <p class="contact-line">
        <svg viewBox="0 0 16 16"><circle cx="8" cy="8" r="6.3" fill="none" stroke="#0e1840" stroke-width="1.5"/><path d="M1.7 8h12.6M8 1.7c-3 3.5-3 9 0 12.6M8 1.7c3 3.5 3 9 0 12.6" fill="none" stroke="#0e1840" stroke-width="1.2"/></svg>
        www.theharborcrestline.com
      </p>
    </div>
  </div>
</section>

</body>
</html>
```